Consulting company requires a logo and business card design

I require a logo/business card design for a new company based in Sexsmith Alberta called TallMarsh Integrity Consulting Ltd. I plan to provide the following services: Construction management/inspection for the oil and gas industry, as well as general consulting for Asset Management, fleet management, etc. Have attached a copy of resume for use as guide for

Target Market(s)

Businesses within the oil and gas production, construction and shipping industry

Industry/Entity Type

Oil And Gas

Contact Information for Business Card

Believe should highlight, services offered, safety, quality,

Logo Text

TallMarsh Integrity Consulting (TMIC) ?

Font styles to use
Script

Requirements
Must have
• Open to all options

```html
<!DOCTYPE html>
<html lang="en">
<head>
<meta charset="utf-8">
<title>TallMarsh Integrity Consulting Ltd. — Business Card</title>
<link href="https://fonts.googleapis.com/css2?family=Source+Sans+3:wght@400;600&display=swap" rel="stylesheet">
<style>
  :root {
    --backdrop: #2b2b2b;
    --card: #161616;
    --card-edge: #0d0d0d;
    --accent: #d81b45;
    --text-light: #f2f2f2;
    --text-muted: #6f6f6f;
    --divider: #3a3a3a;
  }
  * { margin: 0; padding: 0; box-sizing: border-box; }
  html, body { width: 1200px; height: 900px; overflow: hidden; }
  body {
    background: var(--backdrop);
    font-family: "Source Sans 3", "Myriad Pro", Arial, sans-serif;
    display: flex;
    align-items: center;
    justify-content: center;
    gap: 40px;
  }
  .card {
    width: 520px;
    height: 297px;
    background: var(--card);
    border-radius: 18px;
    box-shadow: 0 0 0 1px var(--card-edge);
    position: relative;
  }
  /* Back of card: contact details */
  .card-back { display: flex; }
  .brand-zone {
    width: 210px;
    display: flex;
    flex-direction: column;
    align-items: center;
    justify-content: center;
    gap: 14px;
  }
  .brand-dot {
    width: 54px; height: 54px;
    border-radius: 50%;
    background: var(--accent);
  }
  .brand-initials {
    color: var(--accent);
    font-weight: 600;
    font-size: 26px;
    letter-spacing: 2px;
  }
  .divider {
    width: 1px;
    margin: 34px 0;
    background: linear-gradient(to bottom, transparent, var(--divider) 20%, var(--divider) 80%, transparent);
  }
  .details {
    padding: 44px 0 0 30px;
    color: var(--text-light);
    font-size: 15px;
    line-height: 1.3;
  }
  .person-name { color: var(--accent); font-size: 20px; font-weight: 400; }
  .person-role { margin-bottom: 16px; }
  .address { margin-bottom: 16px; }
  .contact-list { list-style: none; }
  .contact-list li { display: flex; align-items: center; gap: 10px; }
  .contact-list svg { width: 12px; height: 12px; fill: var(--accent); flex: none; }
  /* Front of card: company name */
  .card-front {
    display: flex;
    align-items: center;
    justify-content: center;
  }
  .company-name {
    color: var(--accent);
    font-weight: 600;
    font-size: 25px;
    text-align: center;
    line-height: 1.2;
  }
</style>
</head>
<body>
  <section class="card card-back">
    <div class="brand-zone">
      <span class="brand-dot"></span>
      <span class="brand-initials">TMIC</span>
    </div>
    <div class="divider"></div>
    <div class="details">
      <p class="person-name">Daniel Reeves</p>
      <p class="person-role">Managing Director</p>
      <p class="address">4410 Meadow Road<br>Sexsmith, AB T0H 3C0</p>
      <ul class="contact-list">
        <li>
          <svg viewBox="0 0 24 24"><path d="M6.6 10.8a15.1 15.1 0 0 0 6.6 6.6l2.2-2.2c.3-.3.7-.4 1-.2 1.1.4 2.3.6 3.6.6.6 0 1 .4 1 1V20c0 .6-.4 1-1 1A17 17 0 0 1 3 4c0-.6.4-1 1-1h3.5c.6 0 1 .4 1 1 0 1.3.2 2.5.6 3.6.1.3 0 .7-.2 1z"/></svg>
          044-987 654 321
        </li>
        <li>
          <svg viewBox="0 0 24 24"><path d="M2 5h20v14H2z M2 5l10 8 10-8" /><path d="M3 6.5l9 7 9-7V18H3z" fill="#161616"/></svg>
          info@tallmarsh.com
        </li>
        <li>
          <svg viewBox="0 0 24 24"><path d="M10.6 13.4a1 1 0 0 1 0-1.4l4-4a1 1 0 1 1 1.4 1.4l-4 4a1 1 0 0 1-1.4 0zM7 17a3 3 0 0 1 0-4.2l2.3-2.3L8 9.1 5.6 11.4a5 5 0 0 0 7 7l2.4-2.3-1.4-1.4-2.4 2.3A3 3 0 0 1 7 17zm11.4-11.4a5 5 0 0 0-7 0L9.1 8l1.4 1.4 2.3-2.4a3 3 0 0 1 4.2 4.3l-2.3 2.3 1.4 1.4 2.3-2.3a5 5 0 0 0 0-7z"/></svg>
          www.tallmarshic.com
        </li>
      </ul>
    </div>
  </section>

  <section class="card card-front">
    <p class="company-name">TallMarsh Integrity<br>Consulting Ltd.</p>
  </section>
</body>
</html>
```